Kelvor Engineers: Why you should hire us keepsake

New design. Open to plastic cards. We are an engineering firm that designs cell phone towers and commercial buildings. Please check out our website www.kelvorstruct.com for more details. We want people to remember our card and for it to be useful if possible. We want the same look and feel on these cards to be translated to other marketing material we may need such as brochures.

Target Market(s)

Architects, Developers and Telecommunication Carriers

Industry/Entity Type

Engineering

Contact Information for Business Card

Card with our company colors, logo, and innovative design with elements related to our industry.

Font styles to use
Sans Serif

Colors
9bcb3c
abd036
0255a3

Requirements
Must have
• Sleek and hip design
Nice to have
• Bright lime green and navy coloring that pops with an innovative design.
Should not have
• A basic and boring design

```html
<!DOCTYPE html>
<html lang="en">
<head>
<meta charset="utf-8">
<title>Kelvor Engineers Business Card</title>
<link href="https://fonts.googleapis.com/css2?family=Roboto:wght@400;700&family=Roboto+Condensed:wght@700&display=swap" rel="stylesheet">
<style>
  :root {
    --backdrop: #2b2c2e;
    --card-light: #f4f4f4;
    --card-dark: #17191b;
    --lime: #14f51e;
    --navy: #0b2d5c;
    --grey-text: #555555;
    --white-text: #f2f2f2;
  }
  * { margin: 0; padding: 0; box-sizing: border-box; }
  html, body { width: 1200px; height: 960px; overflow: hidden; }
  body {
    background: var(--backdrop);
    position: relative;
    font-family: "Roboto", Arial, sans-serif;
  }
  .card {
    position: absolute;
    left: 320px;
    width: 602px;
    border-radius: 16px;
    overflow: hidden;
  }
  .card-front {
    top: 100px;
    height: 348px;
    background: var(--card-light);
    text-align: center;
  }
  .brand-name {
    position: absolute;
    top: 145px;
    left: 0; right: 0;
    font-family: "Roboto", Arial, sans-serif;
    font-weight: 700;
    font-size: 56px;
    line-height: 1;
    color: var(--lime);
    letter-spacing: -1px;
  }
  .tagline {
    position: absolute;
    top: 275px;
    left: 0; right: 0;
    display: flex;
    justify-content: center;
    align-items: center;
    gap: 4px;
    font-weight: 700;
    font-size: 14px;
    color: var(--lime);
    letter-spacing: 0.2px;
  }
  .tagline::before, .tagline::after {
    content: "";
    width: 28px;
    height: 2px;
    background: var(--navy);
  }
  .locations {
    position: absolute;
    top: 296px;
    left: 0; right: 0;
    font-size: 15px;
    color: var(--grey-text);
    letter-spacing: 0.4px;
  }
  .card-back {
    top: 493px;
    height: 342px;
    background: var(--card-dark);
  }
  .pattern-area {
    position: absolute;
    top: 0; left: 0;
  }
  .contact-block {
    position: absolute;
    left: 361px;
    top: 188px;
  }
  .person-name {
    font-family: "Roboto Condensed", "Arial Narrow", sans-serif;
    font-weight: 700;
    font-size: 21px;
    color: var(--lime);
    margin-bottom: 10px;
  }
  .contact-list { list-style: none; }
  .contact-list li {
    display: flex;
    align-items: center;
    gap: 10px;
    font-size: 14px;
    line-height: 19px;
    color: var(--white-text);
  }
  .contact-list svg { width: 12px; height: 12px; fill: var(--lime); flex: none; }
</style>
</head>
<body>
  <section class="card card-front">
    <div class="brand-name">Kelvor Engineers</div>
    <div class="tagline">MULTI-DISCIPLINE ENGINEERING</div>
    <div class="locations">Brookvale | Marlow | Eastport | Linden Falls</div>
  </section>

  <section class="card card-back">
    <svg class="pattern-area" width="602" height="342" role="img" aria-label="Diagonal cluster of lime green and navy hexagons">
      <defs>
        <linearGradient id="hexTone" x1="0" y1="0" x2="1" y2="1">
          <stop offset="0" stop-color="#0b2d5c"/>
          <stop offset="0.55" stop-color="#0f5a3a"/>
          <stop offset="1" stop-color="#14c81e"/>
        </linearGradient>
      </defs>
      <polygon points="0,0 562,0 562,28 430,110 360,165 255,235 200,300 160,342 0,342" fill="url(#hexTone)"/>
    </svg>

    <div class="contact-block">
      <div class="person-name">DANA WHITLOW REYES</div>
      <ul class="contact-list">
        <li><svg viewBox="0 0 12 12"><path d="M2.5 0.5l2 2.2-1 1.4c.7 1.6 2 2.9 3.6 3.6l1.4-1 2.2 2-1 2.3C5 11 1 7 .3 1.5z"/></svg>555.014.7391</li>
        <li><svg viewBox="0 0 12 12"><path d="M3 0h6v12H3zM4 1.5v7.5h4V1.5zM5.3 10h1.4v1H5.3z" fill-rule="evenodd"/></svg>555.019.6402</li>
        <li><svg viewBox="0 0 12 12"><path d="M0 2.5h12v7H0zM0 2.5l6 4 6-4v1.2L6 7.7 0 3.7z"/></svg>dreyes@kelvorstruct.com</li>
        <li><svg viewBox="0 0 12 12"><circle cx="6" cy="6" r="5.5"/></svg>www.kelvorstruct.com</li>
      </ul>
    </div>
  </section>
</body>
</html>
```